Recruiting Firm Need Professional, Modern Tri-Fold Brochure for their United States Based Business

-We need a professional, modern TRI-FOLD brochure design that can help generate business for our recruiting firm. We need an impressive brochure.
- Please use the about us website content and attached website content. Website: www.morvellstaffingpartners.example
- Please use logo files attached.
- Please note: This brochure will be the starting point for an upgraded website design so we are NOT looking for a brochure to look like our current website.
- We want potential clients to want to do business with us just based on the brochure look and feel alone.

Target Market(s)

small, medium, and large companies who need administrative, human resources, and accounting talent

Industry/Entity Type

Professional Service

Font styles to use
Serif

Requirements
Must have
• - Professional, Modern TRI-FOLD Brochure Design for United States Based Company
• - Please show diverse group of professionals pictures similar to the ones on our website. One pic must include an African American female and one pic must include an African male. Or both an African American female and male can be include in the group of other races. But All the group photos must be diverse in race and include both male and female.
• - Please show pics of one business professional too
• a diverse group photo would be nice on the front cover...so we can show diversity and inclusion from the start
Should not have
• - Please DO NOT use the same pictures on our website.

```html
<!DOCTYPE html>
<html lang="en">
<head>
<meta charset="utf-8">
<title>Morvell Staffing Partners – Brochure Spread</title>
<link rel="stylesheet" href="https://fonts.googleapis.com/css2?family=Open+Sans:wght@400;600;700&display=swap">
<style>
  :root {
    --red: #a50f12;
    --red-dark: #7d0a0c;
    --black: #151515;
    --paper: #f4f4f6;
    --ink: #3a3a3a;
    --stage: #3b3b3d;
    --photo-tone-a: #e7e7ea;
    --photo-tone-b: #d9d9de;
  }
  * { box-sizing: border-box; margin: 0; padding: 0; }
  html, body { width: 1200px; height: 789px; overflow: hidden; }
  body {
    background: var(--stage);
    font-family: "Open Sans", Arial, sans-serif;
    color: var(--ink);
    position: relative;
  }
  .spread { position: absolute; left: 80px; top: 27px; width: 1040px; height: 735px; display: flex; box-shadow: 0 10px 30px rgba(0,0,0,.45); }
  .page { position: relative; width: 520px; height: 735px; background: var(--paper); overflow: hidden; }
  .page--left { border-right: 1px solid #d5d5d8; }
  .page-photo { position: absolute; inset: 0; background: radial-gradient(ellipse at 50% 45%, var(--photo-tone-b), var(--photo-tone-a) 60%, var(--paper)); opacity: .9; }
  .page-wave { position: absolute; left: 0; top: 0; width: 520px; height: 735px; }
  .intro { position: absolute; left: 40px; top: 42px; width: 440px; font-size: 10.5px; line-height: 1.45; text-align: justify; }

  .services { position: absolute; left: 20px; top: 150px; width: 480px; display: flex; justify-content: space-between; }
  .service { width: 150px; text-align: center; }
  .service-icon { width: 78px; height: 86px; margin: 0 auto 12px; display: block; }
  .service-title { font-size: 13px; font-weight: 700; color: var(--black); padding-bottom: 6px; border-bottom: 1px solid var(--red); margin: 0 14px 10px; }
  .service-text { font-size: 10.5px; line-height: 1.4; }

  .web { position: absolute; left: 30px; top: 690px; color: #fff; font-size: 12px; display: flex; align-items: center; gap: 6px; }

  .tab { position: absolute; left: 0; height: 26px; display: flex; align-items: center; }
  .tab-label { background: var(--red); color: #fff; font-size: 13px; font-weight: 600; padding: 0 16px 0 30px; height: 26px; line-height: 26px; }
  .tab-end { width: 12px; height: 26px; background: var(--black); transform: skewX(-18deg); margin-left: -4px; }
  .block { position: absolute; left: 30px; width: 460px; }
  .heading { color: var(--red); font-size: 15px; font-weight: 700; line-height: 1.3; margin-bottom: 8px; }
  .body-text { font-size: 10.5px; line-height: 1.45; text-align: justify; }
  .checks { list-style: none; font-size: 12px; line-height: 1.4; }
  .checks li { position: relative; padding-left: 22px; margin-bottom: 6px; }
  .checks svg { position: absolute; left: 0; top: 3px; }
</style>
</head>
<body>
<main class="spread">
  <section class="page page--left">
    <div class="page-photo" role="img" aria-label="Faint photograph of diverse business professionals in an office"></div>
    <p class="intro">Morvell Staffing Partners is a premier recruitment firm specializing in full-time, permanent placements of administrative, human resources, and accounting talent. We customize each search based on our client's unique requirements. We provide quality, timely, and efficient services. Our recruiters are highly skilled in identifying, screening, interviewing, and assessing candidates across various industries. We can find the right talent for your hiring needs.</p>

    <div class="services">
      <article class="service">
        <svg class="service-icon" viewBox="0 0 78 86" aria-hidden="true">
          <polygon points="39,2 75,22 75,64 39,84 3,64 3,22" fill="#fff" stroke="var(--red)" stroke-width="2.5"/>
          <rect x="24" y="32" width="30" height="8" fill="#fff" stroke="#777" stroke-width="1.5"/>
          <rect x="19" y="40" width="40" height="16" rx="2" fill="var(--red)"/>
          <rect x="25" y="50" width="28" height="10" fill="#fff" stroke="#777" stroke-width="1.5"/>
        </svg>
        <h3 class="service-title">Administrative</h3>
        <p class="service-text">Behind every successful leader is an awesome assistant. We can provide exceptional support staff who can help you stay organized and run the office smoothly.</p>
      </article>
      <article class="service">
        <svg class="service-icon" viewBox="0 0 78 86" aria-hidden="true">
          <polygon points="39,2 75,22 75,64 39,84 3,64 3,22" fill="#fff" stroke="var(--red)" stroke-width="2.5"/>
          <circle cx="33" cy="36" r="6" fill="var(--red)"/>
          <path d="M21 55 q12 -16 24 0 z" fill="var(--red)"/>
          <circle cx="46" cy="34" r="6" fill="#444"/>
          <path d="M38 52 q8 -15 20 0 z" fill="#444"/>
        </svg>
        <h3 class="service-title">Human Resources</h3>
        <p class="service-text">Human Capital matters. We can provide a results-driven human resources professional who can help take care of your employees and managers while balancing the needs of your company.</p>
      </article>
      <article class="service">
        <svg class="service-icon" viewBox="0 0 78 86" aria-hidden="true">
          <polygon points="39,2 75,22 75,64 39,84 3,64 3,22" fill="#fff" stroke="var(--red)" stroke-width="2.5"/>
          <rect x="24" y="42" width="7" height="14" fill="var(--red)"/>
          <rect x="34" y="32" width="7" height="24" fill="var(--red)"/>
          <rect x="44" y="37" width="7" height="19" fill="#444"/>
          <line x1="20" y1="57" x2="58" y2="57" stroke="#777" stroke-width="1.5"/>
        </svg>
        <h3 class="service-title">Accounting</h3>
        <p class="service-text">If you are seeking an accountant who can keep your company's financial accounts on track, we can help. We have a pipeline of sharp accountants.</p>
      </article>
    </div>

    <svg class="page-wave" viewBox="0 0 520 735" aria-hidden="true">
      <path d="M0 470 C150 520 340 590 520 600 L520 612 C340 604 150 540 0 492 Z" fill="var(--black)"/>
      <path d="M0 492 C150 540 340 604 520 612 L520 630 C340 626 160 570 0 530 Z" fill="var(--red-dark)"/>
      <path d="M0 552 C160 590 340 640 520 652 L520 735 L0 735 Z" fill="var(--red)"/>
    </svg>
    <div class="web">
      <svg width="12" height="12" viewBox="0 0 12 12" aria-hidden="true"><circle cx="6" cy="6" r="5" fill="none" stroke="#fff" stroke-width="1.2"/><path d="M1 6h10M6 1c-3 3-3 7 0 10M6 1c3 3 3 7 0 10" fill="none" stroke="#fff" stroke-width="1"/></svg>
      www.morvellstaffingpartners.example
    </div>
  </section>

  <section class="page page--right">
    <div class="page-photo" role="img" aria-label="Faint photograph of a business team in a meeting"></div>

    <div class="tab" style="top:46px"><span class="tab-label">Who We Are</span><span class="tab-end"></span></div>
    <div class="block" style="top:84px">
      <h2 class="heading">A Top-Notch Resource for Administrative, Human Resources, and Accounting Talent</h2>
      <p class="body-text">Morvell Staffing Partners is a professional search firm that specializes in providing top-notch administrative, human resources, and accounting talent. The cornerstone of our business is to provide best-in-class talent to companies seeking to simplify their recruiting process, increase efficiency, and optimize productivity. We develop a partnership with our client and candidate in order to make the recruitment process a success for both parties.</p>
    </div>

    <div class="tab" style="top:250px"><span class="tab-label">Experience the Morvell Difference</span><span class="tab-end"></span></div>
    <div class="block" style="top:290px">
      <h2 class="heading">We use our proprietary M-Strategy approach to deliver high-quality results.</h2>
      <ul class="checks">
        <li><svg width="13" height="11" viewBox="0 0 13 11" aria-hidden="true"><path d="M1 6l4 4 7-9" fill="none" stroke="var(--red)" stroke-width="2.4"/></svg>Top-Notch Talent. We will only present candidates who meet 90% of your job requirements.</li>
        <li><svg width="13" height="11" viewBox="0 0 13 11" aria-hidden="true"><path d="M1 6l4 4 7-9" fill="none" stroke="var(--red)" stroke-width="2.4"/></svg>Thorough. We listen to your needs and develop a recruiting checklist to make sure we cover all basis.</li>
        <li><svg width="13" height="11" viewBox="0 0 13 11" aria-hidden="true"><path d="M1 6l4 4 7-9" fill="none" stroke="var(--red)" stroke-width="2.4"/></svg>Tenacious. We are passionate and persistent about meeting your expectations.</li>
        <li><svg width="13" height="11" viewBox="0 0 13 11" aria-hidden="true"><path d="M1 6l4 4 7-9" fill="none" stroke="var(--red)" stroke-width="2.4"/></svg>Timely. We deliver quality results on time.</li>
      </ul>
    </div>

    <div class="tab" style="top:482px"><span class="tab-label">A Trusted Recruiting Partner</span><span class="tab-end"></span></div>
    <div class="block" style="top:522px">
      <p class="body-text">We have over 25 years of recruiting and human resources experience. Our recruiters have the expertise, insights, and passion to bring value-added recruiting services to your company. We have track record of excellence.</p>
    </div>

    <svg class="page-wave" viewBox="0 0 520 735" aria-hidden="true">
      <path d="M0 600 C160 620 340 650 520 655 L520 662 C340 660 160 632 0 612 Z" fill="var(--black)"/>
      <path d="M0 612 C160 632 340 660 520 662 L520 668 C340 670 160 650 0 630 Z" fill="var(--red-dark)"/>
      <path d="M0 640 C160 662 340 680 520 680 L520 735 L0 735 Z" fill="var(--red)"/>
    </svg>
  </section>
</main>
</body>
</html>
```